Tech Savy small Business accountant business card design

We need a business card for a new company based in the cloud. We provide tax, business advisory, accounting, information technology solutions and back office functions to small businesses. We offer fixed fee packages with add on services as you need them. By harnessing technology we simplify small business operational processes providing valuable time and information for small business owners to grow their business. In the logo (bluvoria) we want to be able to see bluv and experts. The final design should communicate achieving growth dreams and balance (ie life and $).
Updates
This project has been temporarily placed on hold until I finalize "Tech Savy small Business accountant needs a logo". I invite all designers to submit on this logo project. Once my logo is finalized I will resume this business card contest. Thanks Added Wednesday, March 19, 2014
This project has been temporarily placed on hold until I finalize "Tech Savy small Business accountant logo". I invite all designers to submit on this logo project. Once my logo is finalized I will resume this business card contest. Thanks Added Thursday, March 20, 2014
Target Market(s)
Small Business (Revenue $500,000, more than 3 employees) owners.
Industry/Entity Type
Small Business
Contact Information for Business Card
Marcy Elwind (Principal)
Accountant, Tax Agent.
TEL | 0417 683 912
EMAIL | Marcy.Elwind@bluvoria.com.au
WEB | www.bluvoria.com.au
Look and feel

```html
<!DOCTYPE html>
<html lang="en">
<head>
<meta charset="utf-8">
<title>bluvoria business card</title>
<link href="https://fonts.googleapis.com/css2?family=Open+Sans:wght@400;600;700&display=swap" rel="stylesheet">
<style>
  :root {
    --bg: #ecebe8;
    --card-dark: #0b0b0c;
    --card-light: #ffffff;
    --brand-blue: #1b8fd8;
    --text-light: #d9d9d9;
    --text-muted: #a9a9a9;
    --text-dark: #1c1c1c;
    --divider: #3d6f93;
  }
  * { box-sizing: border-box; margin: 0; padding: 0; }
  html, body {
    width: 1200px; height: 913px; overflow: hidden;
    background: var(--bg);
    font-family: "Open Sans", sans-serif;
  }
  .canvas {
    width: 1200px; height: 913px;
    display: flex; align-items: center; justify-content: center; gap: 40px;
  }
  .card {
    position: relative;
    width: 540px; height: 309px;
    border-radius: 3px;
    box-shadow: 0 6px 18px rgba(0,0,0,0.18);
  }
  .card--back { background: var(--card-dark); }
  .card--front { background: var(--card-light); }

  /* back side */
  .holder {
    position: absolute; right: 52px; top: 78px; text-align: right;
  }
  .holder__name {
    color: var(--brand-blue); font-weight: 700; font-size: 17px; letter-spacing: 0.3px;
  }
  .holder__role {
    color: var(--text-light); font-size: 11.5px; margin-top: 2px;
  }
  .brand-small {
    position: absolute; left: 40px; top: 150px;
  }
  .brand-small__name {
    color: var(--brand-blue); font-weight: 700; font-size: 38px; line-height: 1; letter-spacing: -0.5px;
  }
  .brand-small__tagline {
    color: var(--text-light); font-size: 9.5px; margin-top: 6px;
  }
  .divider {
    position: absolute; left: 262px; top: 142px; width: 1px; height: 68px;
    background: var(--divider);
  }
  .contacts {
    position: absolute; left: 276px; top: 146px; list-style: none;
  }
  .contacts__item {
    display: flex; align-items: center; gap: 7px;
    color: var(--brand-blue); font-size: 11.5px; line-height: 20px;
  }
  .contacts__icon { width: 11px; height: 11px; flex: none; }

  /* front side */
  .brand-large {
    position: absolute; left: 0; right: 0; top: 100px; text-align: center;
  }
  .brand-large__name {
    color: var(--brand-blue); font-weight: 700; font-size: 76px; line-height: 1; letter-spacing: -1.5px;
  }
  .brand-large__tagline {
    color: var(--text-dark); font-weight: 600; font-size: 17px; margin-top: 8px;
  }
</style>
</head>
<body>
<main class="canvas">
  <section class="card card--back">
    <div class="holder">
      <p class="holder__name">MARCY ELWIND (Principal)</p>
      <p class="holder__role">Accountant, Tax Agent</p>
    </div>
    <div class="brand-small">
      <p class="brand-small__name">bluvoria</p>
      <p class="brand-small__tagline">Your business and accounting partner</p>
    </div>
    <div class="divider"></div>
    <ul class="contacts">
      <li class="contacts__item">
        <svg class="contacts__icon" viewBox="0 0 12 12"><path d="M2.5 1 L4.5 1 L5.3 3.5 L4 4.5 Q5 7 7.5 8 L8.5 6.7 L11 7.5 L11 9.5 Q10.5 11 9 11 Q1 10 1 3 Q1 1.5 2.5 1 Z" fill="var(--text-light)"/></svg>
        0417 683 912
      </li>
      <li class="contacts__item">
        <svg class="contacts__icon" viewBox="0 0 12 12" fill="none" stroke="var(--text-light)" stroke-width="1.1"><circle cx="6" cy="6" r="5"/><ellipse cx="6" cy="6" rx="2.2" ry="5"/><line x1="1" y1="6" x2="11" y2="6"/></svg>
        www.bluvoria.com.au
      </li>
      <li class="contacts__item">
        <svg class="contacts__icon" viewBox="0 0 12 12" fill="none" stroke="var(--text-light)" stroke-width="1.1"><rect x="1" y="2.5" width="10" height="7"/><polyline points="1,2.5 6,6.5 11,2.5"/></svg>
        Marcy.Elwind@bluvoria.com.au
      </li>
    </ul>
  </section>

  <section class="card card--front">
    <div class="brand-large">
      <p class="brand-large__name">bluvoria</p>
      <p class="brand-large__tagline">Your business and accounting partner</p>
    </div>
  </section>
</main>
</body>
</html>
```